Vantrell Air Business Card Design

Design new, 2 sides, business cards for a residential and light commercial heating, air conditioning contractor.

Target Market(s)

Homeowners, small businesses

Industry/Entity Type

Business

Contact Information for Business Card

Dominic Westerhall
Phone - 862-415-2736
Email
Address - PO box 518
Brightwater NJ 07912
Website - www.VantrellAirLLC.example

Requirements
Must have
• logo, company colors, standard size with no die cut, so I can use nova stamp

```html
<!DOCTYPE html>
<html lang="en">
<head>
<meta charset="utf-8">
<title>Vantrell Air Business Card</title>
<link rel="stylesheet" href="https://fonts.googleapis.com/css2?family=Lato:wght@400;700;900&display=swap">
<style>
  :root {
    --orange: #f28a30;
    --wine: #8e1b2a;
    --ink: #7a7a7a;
    --rule: #6d6d6d;
    --paper: #ffffff;
    --backdrop: #ecebea;
    --on-orange: #ffffff;
  }
  * { margin: 0; padding: 0; box-sizing: border-box; }
  html, body { width: 1200px; height: 880px; overflow: hidden; }
  body {
    background: var(--backdrop);
    font-family: 'Lato', sans-serif;
    display: flex;
    flex-direction: column;
    align-items: center;
    justify-content: center;
    gap: 40px;
  }
  .card {
    width: 665px;
    height: 380px;
    position: relative;
    box-shadow: 0 4px 14px rgba(0,0,0,0.12);
    overflow: hidden;
  }

  /* Front side */
  .card-front { background: var(--paper); }
  .card-front .base-band {
    position: absolute; left: 0; right: 0; bottom: 0; height: 14px;
    background: var(--orange);
  }
  .brand-mark {
    position: absolute; left: 150px; top: 44px;
    display: flex; align-items: center; gap: 10px;
  }
  .brand-mark .dot { width: 16px; height: 16px; border-radius: 50%; background: var(--wine); flex: none; }
  .brand-mark .brand-name {
    font-weight: 900; font-size: 26px; color: var(--wine); letter-spacing: 0.5px; white-space: nowrap;
  }
  .person { position: absolute; left: 120px; top: 110px; }
  .person-name { font-weight: 700; font-size: 27px; color: var(--wine); white-space: nowrap; }
  .person-title { font-weight: 700; font-size: 20px; color: var(--orange); margin-top: 2px; white-space: nowrap; }
  .divider {
    position: absolute; left: 270px; right: 30px; top: 160px;
    height: 2px; background: var(--rule);
  }
  .contact-list {
    position: absolute; left: 82px; top: 190px;
    list-style: none; display: flex; flex-direction: column; gap: 6px;
  }
  .contact-list li {
    display: flex; align-items: center; gap: 12px;
    font-size: 17px; color: var(--ink); white-space: nowrap;
  }
  .contact-list svg { width: 14px; height: 14px; flex: none; }
  .address {
    position: absolute; right: 30px; bottom: 40px;
    display: flex; align-items: center; gap: 12px;
  }
  .address-lines { text-align: right; font-size: 17px; color: var(--ink); line-height: 1.3; }
  .address svg { width: 16px; height: 20px; }

  /* Back side */
  .card-back { background: var(--orange); }
  .card-back .brand-mark {
    left: 0; right: 0; top: 145px; justify-content: center; gap: 14px;
  }
  .card-back .brand-mark .dot { background: var(--on-orange); width: 22px; height: 22px; }
  .card-back .brand-mark .brand-name { color: var(--on-orange); font-size: 46px; }
  .card-back .site {
    position: absolute; left: 0; right: 0; bottom: 40px;
    text-align: center; color: var(--on-orange); font-size: 18px;
  }
</style>
</head>
<body>
  <section class="card card-front">
    <div class="brand-mark">
      <span class="dot"></span>
      <span class="brand-name">Vantrell Air</span>
    </div>
    <div class="person">
      <div class="person-name">Dominic Westerhall</div>
      <div class="person-title">Founder &amp; CEO</div>
    </div>
    <div class="divider"></div>
    <ul class="contact-list">
      <li>
        <svg viewBox="0 0 24 24"><path fill="#f28a30" d="M6.6 10.8a15 15 0 0 0 6.6 6.6l2.2-2.2c.3-.3.7-.4 1-.2 1.1.4 2.3.6 3.6.6.6 0 1 .4 1 1V20c0 .6-.4 1-1 1A17 17 0 0 1 3 4c0-.6.4-1 1-1h3.5c.6 0 1 .4 1 1 0 1.3.2 2.5.6 3.6.1.3 0 .7-.2 1z"/></svg>
        862-415-2736
      </li>
      <li>
        <svg viewBox="0 0 24 24"><path fill="#f28a30" d="M2 5h20v14H2z"/><path fill="none" stroke="#fff" stroke-width="2" d="M2 5l10 8 10-8"/></svg>
        info@VantrellAirLLC.example
      </li>
      <li>
        <svg viewBox="0 0 24 24"><g fill="none" stroke="#f28a30" stroke-width="2"><circle cx="12" cy="12" r="10"/><path d="M2 12h20M12 2c3 3 3 17 0 20M12 2c-3 3-3 17 0 20"/></g></svg>
        www.VantrellAirLLC.example
      </li>
    </ul>
    <div class="address">
      <div class="address-lines">
        <div>PO box 518</div>
        <div>Brightwater NJ 07912</div>
      </div>
      <svg viewBox="0 0 16 20"><path fill="#f28a30" d="M8 0a7 7 0 0 0-7 7c0 5 7 13 7 13s7-8 7-13a7 7 0 0 0-7-7z"/><circle cx="8" cy="7" r="2.6" fill="#fff"/></svg>
    </div>
    <div class="base-band"></div>
  </section>

  <section class="card card-back">
    <div class="brand-mark">
      <span class="dot"></span>
      <span class="brand-name">Vantrell Air</span>
    </div>
    <div class="site">www.VantrellAirLLC.example</div>
  </section>
</body>
</html>
```